BrindleStaffing Business Card Design

We are a staffing company finding positions for dedicated nurses and physicians.

Target Market(s)

Business Professionals

Industry/Entity Type

Staffing

Contact Information for Business Card

Gordon Pratley
Chairman
417 39th Avenue South
SAINT PETERSBURG FL 33712
813-555-4172 Mobile
813-555-8036 Fax
gpratley@brindlestaffing.com
www.brindlestaffing.com

Font styles to use
Sans Serif

Colors
fbee3e
f04a50
f37122

Requirements
Must have
• Logo Attached, see colors below. We'd like to see Yellow, Orange and Red.

```html
<!DOCTYPE html>
<html lang="en">
<head>
<meta charset="utf-8">
<title>BrindleStaffing Business Card</title>
<link rel="stylesheet" href="https://fonts.googleapis.com/css2?family=Open+Sans:wght@400;600;700&display=swap">
<style>
  :root {
    --yellow: #fbee3e;
    --red: #f04a50;
    --orange: #f37122;
    --white: #ffffff;
    --black: #000000;
    --card-edge: #b5b5b5;
    --bg-light: #96979b;
    --bg-dark: #3f3e40;
  }
  html, body {
    margin: 0;
    padding: 0;
    width: 1200px;
    height: 1134px;
    overflow: hidden;
  }
  body {
    position: relative;
    background: radial-gradient(circle at 50% 50%, var(--bg-light) 0%, #6a6a6d 45%, var(--bg-dark) 100%);
    font-family: "Open Sans", Arial, sans-serif;
  }
  .card {
    position: absolute;
    width: 716px;
    height: 409px;
    border-radius: 46px;
    overflow: hidden;
    box-sizing: border-box;
  }
  .card--front {
    left: 85px;
    top: 100px;
    background: var(--white);
    border: 1px solid var(--card-edge);
  }
  .card--back {
    left: 366px;
    top: 578px;
    background: var(--black);
  }
  .brand {
    position: absolute;
    display: flex;
    align-items: center;
    gap: 10px;
    white-space: nowrap;
  }
  .brand-dot {
    flex: none;
    border-radius: 50%;
    background: var(--yellow);
  }
  .brand-name {
    margin: 0;
    font-weight: 700;
    color: var(--orange);
    letter-spacing: -1px;
  }
  .card--front .brand {
    left: 28px;
    top: 176px;
  }
  .card--front .brand-dot { width: 16px; height: 16px; }
  .card--front .brand-name { font-size: 40px; line-height: 56px; }
  .card--back .brand {
    left: 0;
    width: 100%;
    justify-content: center;
    top: 140px;
  }
  .card--back .brand-dot { width: 24px; height: 24px; }
  .card--back .brand-name { font-size: 60px; line-height: 84px; }
  .web-strip {
    position: absolute;
    left: 381px;
    top: 60px;
    width: 32px;
    height: 289px;
    background: var(--red);
    display: flex;
    align-items: center;
    justify-content: center;
  }
  .web-strip span {
    writing-mode: vertical-rl;
    transform: rotate(180deg);
    color: var(--white);
    font-size: 16px;
    letter-spacing: 1.4px;
    white-space: nowrap;
  }
  .contact-panel {
    position: absolute;
    left: 418px;
    top: 60px;
    width: 300px;
    height: 289px;
    background: var(--orange);
    color: var(--white);
    box-sizing: border-box;
    padding: 28px 0 0 14px;
  }
  .person-name {
    margin: 0;
    font-size: 22px;
    font-weight: 700;
    line-height: 28px;
  }
  .person-title {
    margin: 0;
    font-size: 19px;
    line-height: 25px;
  }
  .contact-list {
    list-style: none;
    margin: 14px 0 0;
    padding: 0;
    font-size: 16px;
    line-height: 28px;
  }
  .contact-list li {
    display: flex;
    align-items: center;
    gap: 9px;
    white-space: nowrap;
  }
  .contact-list svg {
    width: 17px;
    height: 17px;
    flex: none;
  }
  .address {
    margin: 14px 0 0 2px;
    font-style: normal;
    font-size: 16px;
    line-height: 26px;
  }
  .back-url {
    position: absolute;
    left: 0;
    width: 100%;
    top: 256px;
    text-align: center;
    margin: 0;
    font-size: 21px;
    letter-spacing: 2.5px;
    color: var(--white);
  }
  .back-url .accent-yellow { color: var(--yellow); font-weight: 600; }
  .back-url .accent-orange { color: var(--orange); font-weight: 600; }
</style>
</head>
<body>
  <section class="card card--front" aria-label="Business card front">
    <div class="brand">
      <span class="brand-dot"></span>
      <p class="brand-name">BrindleStaffing</p>
    </div>
    <div class="web-strip"><span>www.brindlestaffing.com</span></div>
    <div class="contact-panel">
      <p class="person-name">Gordon Pratley</p>
      <p class="person-title">Chairman</p>
      <ul class="contact-list">
        <li>
          <svg viewBox="0 0 18 18" aria-hidden="true">
            <circle cx="9" cy="9" r="8" fill="none" stroke="#fff" stroke-width="1.4"/>
            <path d="M6.5 4.8c.6-.4 1.2 0 1.4.5l.5 1.3c.2.5-.1.9-.5 1.1-.2.8.6 2.2 1.4 2.6.4-.3.9-.4 1.2 0l.9 1c.4.5.2 1-.3 1.3-2.6 1.4-6.6-5.5-4.6-7.8z" fill="#fff"/>
          </svg>
          813-555-4172 Mobile
        </li>
        <li>
          <svg viewBox="0 0 18 18" aria-hidden="true">
            <rect x="5" y="2" width="8" height="5" fill="none" stroke="#fff" stroke-width="1.4"/>
            <rect x="2" y="7" width="14" height="6" rx="1" fill="#fff"/>
            <rect x="5" y="11" width="8" height="5" fill="#fff" stroke="#f37122" stroke-width="1.2"/>
          </svg>
          813-555-8036 Fax
        </li>
        <li>
          <svg viewBox="0 0 18 18" aria-hidden="true">
            <path d="M1.5 7.5 9 3l7.5 4.5V15h-15z" fill="#fff"/>
            <path d="M1.5 7.5 9 12l7.5-4.5" fill="none" stroke="#f37122" stroke-width="1.4"/>
          </svg>
          gpratley@brindlestaffing.com
        </li>
      </ul>
      <address class="address">417 39th Avenue South<br>Saint petersburg fl 33712</address>
    </div>
  </section>

  <section class="card card--back" aria-label="Business card back">
    <div class="brand">
      <span class="brand-dot"></span>
      <p class="brand-name">BrindleStaffing</p>
    </div>
    <p class="back-url">www.<span class="accent-yellow">brindle</span><span class="accent-orange">staffing</span>.com</p>
  </section>
</body>
</html>
```